White Paper and One-Page Advertisement for TELVORISH-QM

I need both documents to be better formatted and designed so they look professional, not something someone with mediocre word skills put together. They will go out to 1000s of industry professionals, and they need to look sharp. I need them to have my company's color palate logo, and branding on it similar to how it is now, but better. Please do not change any of the written content, but it can be arranged in any other format you think is better. Smart art and things i've already used can be omitted in favor of better designs. The developer is free to use their creativity. White paper should not be longer than the three pages unless necessary.

Target Market(s)

Life Sciences supply chain professionals

Colors
33b8a4
0592cd
9bcb3c
fbee3e
3277b5

Requirements
Must have
• Must be professional looking and not look like something done in word. Please use the color palate as seen on the documents.
Should not have
• Any changes to the written content.

```html
<!DOCTYPE html>
<html lang="en">
<head>
<meta charset="utf-8">
<title>White Paper Spread</title>
<link href="https://fonts.googleapis.com/css2?family=Roboto+Condensed:wght@400;700&family=Arimo:wght@400;700&display=swap" rel="stylesheet">
<style>
:root{
  --bg:#3c3c3e;
  --paper:#ffffff;
  --ink:#3a3d40;
  --head:#2f3437;
  --teal:#33b8a4;
  --blue:#0592cd;
  --green:#9bcb3c;
  --yellow:#fbee3e;
  --navy:#3277b5;
  --lime:#c4cc36;
  --cyan:#2cbfdc;
  --sky:#7fcde0;
  --band:#5aafc3;
  --deepteal:#0f9a80;
}
*{margin:0;padding:0;box-sizing:border-box}
html,body{width:1200px;height:900px;overflow:hidden;background:var(--bg)}
body{position:relative;font-family:"Arimo",Arial,sans-serif;color:var(--ink)}
.page{position:absolute;top:99px;width:496px;height:701px;background:var(--paper);overflow:hidden}
.page--left{left:82px}
.page--right{left:622px}
.page__bg{position:absolute;inset:0;width:100%;height:100%}
.col{position:absolute;width:205px;font-size:8.4px;line-height:11.2px}
.col p{text-align:justify}
.kicker{font-family:"Roboto Condensed",sans-serif;font-weight:700;font-size:11px;color:var(--head);letter-spacing:.2px;margin:0 0 6px}
.sub{font-family:"Arimo",sans-serif;font-weight:700;font-size:10.5px;color:var(--head);margin:9px 0 4px}
.list{list-style:none}
.list li{position:relative;padding-left:9px;margin-bottom:1.5px;text-align:justify}
.list li::before{content:"";position:absolute;left:0;top:3px;width:4px;height:4px;border:1px solid #666;border-radius:50%;background:radial-gradient(#666 35%,transparent 40%)}
.ring{position:absolute;left:278px;top:146px;width:165px;height:165px}
.barriers{position:absolute;left:23px;top:238px;width:449px;height:279px;background:linear-gradient(180deg,#63b7c8,#4fa7bb)}
.barriers__title{height:36px;background:var(--green);color:#fff;font-family:"Roboto Condensed",sans-serif;font-weight:700;font-size:17px;text-align:center;line-height:36px}
.barrier{position:absolute;width:212px}
.barrier__tag{position:relative;height:24px;color:#fff;font-family:"Roboto Condensed",sans-serif;font-weight:700;font-size:11px;line-height:24px;padding-left:9px}
.barrier__tag svg{position:absolute;left:0;top:-3px;width:212px;height:30px;z-index:0}
.barrier__tag span{position:relative;z-index:1}
.barrier__text{color:#fff;font-size:8px;line-height:10.2px;padding:4px 22px 0 14px;text-align:justify}
</style>
</head>
<body>

<section class="page page--left">
  <svg class="page__bg" viewBox="0 0 496 701" preserveAspectRatio="none" aria-hidden="true">
    <defs>
      <linearGradient id="warm" x1="0" y1="0" x2="1" y2="1"><stop offset="0" stop-color="#eef0d8"/><stop offset="1" stop-color="#ffffff"/></linearGradient>
      <linearGradient id="cool" x1="0" y1="0" x2="0" y2="1"><stop offset="0" stop-color="#d6edf1"/><stop offset="1" stop-color="#a9d5df"/></linearGradient>
    </defs>
    <polygon points="0,0 300,0 0,300" fill="url(#warm)"/>
    <polygon points="0,480 240,701 0,701" fill="url(#cool)" opacity=".9"/>
    <polygon points="496,390 496,701 180,701" fill="url(#cool)"/>
    <polygon points="0,120 140,0 496,0 496,100 250,360" fill="#f3f8f9" opacity=".6"/>
  </svg>

  <div class="col" style="left:34px;top:38px">
    <ul class="list">
      <li>High CoGS due to materials write-downs</li>
      <li>High inventory carrying costs</li>
      <li>Greater business continuity risk</li>
      <li>High Disposal costs</li>
      <li>Larger environmental footprint</li>
      <li>Stock-out materials</li>
    </ul>
    <h3 class="sub">Who?</h3>
    <ul class="list"><li>FDA Regulated Industries, Procurement, Quality, Production, and Finance.</li></ul>
    <h3 class="sub">Where and When?</h3>
    <ul class="list">
      <li>Commercial &amp; clinical production, R&amp;D, sourcing/purchasing, production planning, quality testing, etc.</li>
      <li>Volatile demand periods, e.g., product intro growth, decline, seasonality, economic uncertainty, and unforeseen events.</li>
    </ul>
    <h3 class="sub">How do we know it's there?</h3>
    <ul class="list"><li>We physically see it taking place, and it's in our data.</li></ul>

    <h2 class="kicker" style="margin-top:22px">TRIPLE BOTTOM LINE IMPACT</h2>
    <h3 class="sub">Financial</h3>
    <h3 class="sub">Vendors/Sellers</h3>
    <ul class="list"><li>Higher write-downs/offs and 3rd party disposal fees</li></ul>
    <h3 class="sub">Buyers</h3>
    <ul class="list">
      <li>Lost sales - stock-outs</li>
      <li>Inflated market value of materials &amp; supplier expedition fees</li>
      <li>High SS cost due to bullwhip effect</li>
    </ul>
    <h3 class="sub">Environment</h3>
    <ul class="list">
      <li>Greater contribution to global warming through landfill addition, incineration, inactivation, and energy consumption</li>
      <li>Non compliance with ISO 14000 &amp; 9000 and B-Corp Status</li>
    </ul>
    <h3 class="sub">Society</h3>
    <ul class="list">
      <li>Lost community trust - high environment and consumer costs.</li>
      <li>Less innovation, collaboration, and supply chain optimization</li>
    </ul>
  </div>

  <div class="col" style="left:258px;top:34px;width:204px">
    <h2 class="kicker">CURRENT STATE</h2>
    <h2 class="kicker">EXTERNAL SOLUTIONS</h2>
    <p>Pharma and other FDA industries spend considerable energy on reducing waste. A plethora of techniques are employed to mitigate, prepare for, respond to, and recover from the bullwhip effect, which is one of the leading causes of write-downs and waste. However, such efforts are predicated on:</p>
  </div>

  <svg class="ring" viewBox="-85 -85 170 170" role="img" aria-label="Bullwhip influences: forecast accuracy, supplier reliability, external environment, process variability">
    <defs>
      <path id="arcTL" d="M -62,-6 A 62 62 0 0 1 -6,-62"/>
      <path id="arcTR" d="M 6,-62 A 62 62 0 0 1 62,-6"/>
      <path id="arcBR" d="M 62,6 A 62 62 0 0 1 6,62"/>
      <path id="arcBL" d="M -6,62 A 62 62 0 0 1 -62,6"/>
      <path id="tTL" d="M -58,-3 A 59 59 0 0 1 -3,-58"/>
      <path id="tTR" d="M 3,-58 A 59 59 0 0 1 58,-3"/>
      <path id="tBR" d="M 62,3 A 62 62 0 0 1 3,62"/>
      <path id="tBL" d="M -3,62 A 62 62 0 0 1 -62,3"/>
    </defs>
    <use href="#arcTL" fill="none" stroke="var(--green)" stroke-width="30"/>
    <use href="#arcTR" fill="none" stroke="#d3de3a" stroke-width="30"/>
    <use href="#arcBR" fill="none" stroke="var(--cyan)" stroke-width="30"/>
    <use href="#arcBL" fill="none" stroke="var(--teal)" stroke-width="30"/>
    <g font-family="Roboto Condensed, sans-serif" font-weight="700" font-size="7.5" fill="#fff" letter-spacing=".4">
      <text><textPath href="#tTL" startOffset="50%" text-anchor="middle">FORECAST ACCURACY</textPath></text>
      <text><textPath href="#tTR" startOffset="50%" text-anchor="middle">SUPPLIER RELIABILITY</textPath></text>
      <text><textPath href="#tBR" startOffset="50%" text-anchor="middle">EXTERNAL ENVIRONMENT</textPath></text>
      <text><textPath href="#tBL" startOffset="50%" text-anchor="middle">PROCESS VARIABILITY</textPath></text>
    </g>
    <g font-family="Roboto Condensed, sans-serif" font-weight="700" font-size="12.5" fill="var(--blue)" text-anchor="middle">
      <text y="-3">BULLWHIP</text>
      <text y="12">INFLUENCES</text>
    </g>
  </svg>

  <div class="col" style="left:258px;top:312px;width:204px">
    <p>While not fruitless, attempts to mitigate the above external influences are extremely unpredictable and have never solved pharma's write-down, inefficiency, stock-out, and environmental problems.</p>
    <h2 class="kicker" style="margin-top:10px">INTERNAL SOLUTIONS</h2>
    <p>The next effort involves reducing obsolence by making use of materials within the firm. Typically, interplant demand is the only outlet to optimize surplus earmarked for a reserve/write-down. Even this involves may of the same regulatory compliance, quality, and economic challenges. Facilitating this takes time, resources, and does not provide a broad network to utilize.</p>
    <h2 class="kicker" style="margin-top:10px">ENVIRONMENTAL SOLUTIONS</h2>
    <p>FDA industries, like most others, make attempts to reuse, recycle, and convert to energy where applicable. However, they're unable to conduct these activities for perishable, expiring, and/or consumable materials.</p>
    <h2 class="kicker" style="margin-top:10px">UNDESIRABLE SOLUTIONS</h2>
    <p>Unfortunately, third party disposal (frequently landfill) is typically the first and most popular option as perishable, expiring, and complex materials are generally unable to be reused or recycled. These disposals come in many forms to include responsible landfills, incineration, inactivation, etc.</p>
  </div>
</section>

<section class="page page--right">
  <svg class="page__bg" viewBox="0 0 496 701" preserveAspectRatio="none" aria-hidden="true">
    <defs>
      <linearGradient id="warm2" x1="0" y1="0" x2="1" y2="1"><stop offset="0" stop-color="#eef0d8"/><stop offset="1" stop-color="#ffffff"/></linearGradient>
      <linearGradient id="cool2" x1="0" y1="0" x2="0" y2="1"><stop offset="0" stop-color="#e0f1f4"/><stop offset="1" stop-color="#a9d5df"/></linearGradient>
    </defs>
    <polygon points="0,0 260,0 0,240" fill="url(#warm2)"/>
    <polygon points="300,0 496,0 496,200" fill="#e4f2f5"/>
    <polygon points="0,520 190,701 0,701" fill="url(#cool2)"/>
    <polygon points="496,480 496,701 300,701" fill="url(#cool2)"/>
    <polygon points="190,701 300,600 400,701" fill="#ffffff"/>
  </svg>

  <div class="col" style="left:33px;top:32px">
    <h2 class="kicker">OVERALL</h2>
    <p>Industries spend much capital and resources to reduce write-downs in an environment where the bullwhip effect reigns supreme. Mitigations to this effect are attempted but only partially successful or sustainable.</p>
    <h2 class="kicker" style="margin-top:7px">REFINED PROBLEM</h2>
    <p style="color:#222">There is no clear market leader that helps organizations optimize waste, collaborative to reduce it, and market more quality materials to more firms whether for research, manufacturing, or donations. This marketplace must be regulated and all participates properly vetted and authenticated. Accounts must be created to enable companies to post materials and request for information/quotes. Additionally, this marketplace must facilitate</p>
  </div>

  <div class="col" style="left:257px;top:36px">
    <p>collaborative relationships between companies thathelp them reduce supply chain costs. It must quickly, economically, compliantly, and legally facilitatethose exchanges. Lack of this market leader may have enabled the waste problem as seen today.</p>
    <h3 class="sub" style="margin-top:7px">Contemporary Operating Environment</h3>
    <ul class="list">
      <li>Constant pressure from global competition, increasing customer and governmental demand on price, more regulatory scrutiny, and a relentless societal pursuit of sustainability are starting to erode what were once high margins for Pharma.</li>
      <li>Regulators are cooperative and open to solutions.</li>
      <li>Exchanges and consortiums are not typically leveraged in Pharma.</li>
      <li>Pharma continues to struggle with the bullwhip effect.</li>
    </ul>
  </div>

  <div class="barriers">
    <div class="barriers__title">BARRIERS</div>

    <div class="barrier" style="left:6px;top:46px">
      <div class="barrier__tag"><svg viewBox="0 0 212 30" preserveAspectRatio="none"><polygon points="0,3 196,3 196,0 212,15 196,30 196,27 0,27" fill="#8fcd22"/></svg><span>COMPLIANCE</span></div>
      <p class="barrier__text">It is the responsibility of manufacturers to provide customers/patients with quality, safe, and efficacious products. However, there is a misperception that high quality cGMP compliant materials, parts, and equipment cannot be sourced from aftermarket exchanges and consortiums.</p>
    </div>
    <div class="barrier" style="left:230px;top:46px">
      <div class="barrier__tag"><svg viewBox="0 0 212 30" preserveAspectRatio="none"><polygon points="0,3 196,3 196,0 212,15 196,30 196,27 0,27" fill="var(--lime)"/></svg><span>LIABILITY</span></div>
      <p class="barrier__text">Contractual agreements with suppliers have clauses to resolve issues dealing with poor quality. There is a misperception that these agreements cannot implemented at both the marketplace and transactional level.</p>
    </div>
    <div class="barrier" style="left:6px;top:146px">
      <div class="barrier__tag"><svg viewBox="0 0 212 30" preserveAspectRatio="none"><polygon points="0,3 196,3 196,0 212,15 196,30 196,27 0,27" fill="var(--deepteal)"/></svg><span>ECONOMICS</span></div>
      <p class="barrier__text">Exchanges can be difficult due to time/effort. A sanctioned marketplace can provide the structure to make it easy.</p>
    </div>
    <div class="barrier" style="left:230px;top:146px">
      <div class="barrier__tag"><svg viewBox="0 0 212 30" preserveAspectRatio="none"><polygon points="0,3 196,3 196,0 212,15 196,30 196,27 0,27" fill="var(--sky)"/></svg><span>SUSTAINABILITY</span></div>
      <p class="barrier__text">Firms have not discovered how to leverage exchanges to reduce environmental footprint and enable industry certifications as well as community trust.</p>
    </div>
    <div class="barrier" style="left:6px;top:218px">
      <div class="barrier__tag"><svg viewBox="0 0 212 30" preserveAspectRatio="none"><polygon points="0,3 196,3 196,0 212,15 196,30 196,27 0,27" fill="var(--blue)"/></svg><span>CONFIDENCE</span></div>
      <p class="barrier__text">Trust is critical to firms. They should know that a marketplace has properly vetted members with KPI data for analysis.</p>
    </div>
    <div class="barrier" style="left:230px;top:218px">
      <div class="barrier__tag"><svg viewBox="0 0 212 30" preserveAspectRatio="none"><polygon points="0,3 196,3 196,0 212,15 196,30 196,27 0,27" fill="var(--green)"/></svg><span>SPEED</span></div>
      <p class="barrier__text">Exchanges should be fast. An innovative marketplace can ensure quick exchanges.</p>
    </div>
  </div>

  <div class="col" style="left:33px;top:534px">
    <h2 class="kicker">ROOT CAUSE &amp; PARADIGM SHIFT</h2>
    <p>Comfort in the status quo has enabled a culture of waste. With life science margins so high, it hasn't been a priority to solve. Additionally, there hasn't been an effective means to deal with waste. This limits the industry's ability to leverage these marketplaces. Finally, misperceived issues or liability and quality have strained innovation; all solvable problems.</p>
    <h3 class="sub" style="margin-top:8px">Future State</h3>
    <p>Creation of Private Virtual Life Sciences Multi-Vendor Marketplace &amp; Consortiumwhere researchers,</p>
  </div>

  <div class="col" style="left:257px;top:537px">
    <p>manufacturers, and original-end manufacturers can create a simple storefront for their organization and transact materials, equipment, parts, and collaborative relationships in a compliant and professional environment. This marketplace uses a series of software logic that leverages auditing capabilities of buyers and sellers by making FDA required data and documentation visible and subject to ALCOA-Plus, thus enabling transactions in a fast and compliant manner. This logic then automates contracts for digital signature in a part 11 compliant package.</p>
  </div>
</section>

</body>
</html>
```